Business Card for Professional Photographer

I'm looking for an eye catching modern clean design that compliments my logo/ website fonts & colours.
I specialise in architecture, corporate & commercial photography so I'm marketing to professional clients rather than portrait / wedding clients.

I would prefer to not have a solid black design.

My logo brand guide is as follows :

Main front font. : Reislust
Main font colour : #fff
Slogan front font : Ubuntu Bold
Monogram front font : Venti Medium
Container colour : #fff

I need print ready files in pdf .png & .eps formats.

Included in the files below are some screen grabs as reference to font & colours etc.

```html
<!DOCTYPE html>
<html lang="en">
<head>
<meta charset="UTF-8">
<title>Lumen Frame — Business Card</title>
<link rel="stylesheet" href="https://fonts.googleapis.com/css2?family=Quicksand:wght@400&family=Ubuntu:wght@700&family=Open+Sans:wght@400;700&display=swap">
<style>
  :root {
    --backdrop: #9c9c9c;
    --card: #1e1e1e;
    --card-edge: #262626;
    --gold: #d6ab5a;
    --white: #ffffff;
  }
  html, body {
    margin: 0;
    padding: 0;
    overflow: hidden;
  }
  body {
    width: 1049px;
    height: 1200px;
    background: var(--backdrop);
    position: relative;
    font-family: "Open Sans", sans-serif;
  }
  .card {
    position: absolute;
    left: 163px;
    width: 722px;
    height: 412px;
    border-radius: 26px;
    background: var(--card);
    overflow: hidden;
  }
  .card--front { top: 141px; }
  .card--back  { top: 647px; }

  /* Front */
  .front-brand {
    position: absolute;
    top: 165px;
    left: 0;
    right: 0;
    text-align: center;
  }
  .front-brand__name {
    font-family: "Quicksand", sans-serif;
    font-weight: 400;
    font-size: 43px;
    letter-spacing: 0.14em;
    color: var(--white);
    line-height: 1;
    margin: 0 0 0 0.14em;
  }
  .tagline {
    font-family: "Ubuntu", sans-serif;
    font-weight: 700;
    color: var(--gold);
    margin: 0;
  }
  .front-brand .tagline {
    font-size: 15px;
    letter-spacing: 0.3em;
    margin-top: 16px;
  }

  /* Back */
  .back-brand {
    position: absolute;
    top: 88px;
    left: 176px;
    display: flex;
    align-items: center;
    gap: 40px;
  }
  .brand-dot {
    width: 72px;
    height: 72px;
    border-radius: 50%;
    border: 4px solid var(--gold);
    box-sizing: border-box;
  }
  .back-brand__name {
    font-family: "Quicksand", sans-serif;
    font-weight: 400;
    font-size: 28px;
    letter-spacing: 0.14em;
    color: var(--white);
    line-height: 1;
    margin: 0;
  }
  .back-brand .tagline {
    font-size: 10px;
    letter-spacing: 0.25em;
    margin-top: 8px;
  }
  .person {
    position: absolute;
    right: calc(722px - 333px);
    top: 272px;
    text-align: right;
  }
  .person__name {
    font-weight: 700;
    font-size: 29px;
    color: var(--gold);
    line-height: 1.1;
    margin: 0;
  }
  .person__role {
    font-size: 19px;
    color: var(--white);
    margin: 2px 0 0;
  }
  .divider {
    position: absolute;
    left: 356px;
    top: 275px;
    width: 2px;
    height: 70px;
    background: var(--gold);
  }
  .contact {
    position: absolute;
    left: 374px;
    top: 268px;
    list-style: none;
    margin: 0;
    padding: 0;
  }
  .contact__item {
    display: flex;
    align-items: center;
    gap: 5px;
    font-size: 20px;
    color: var(--white);
    line-height: 26px;
  }
  .contact__icon {
    width: 16px;
    height: 16px;
    flex: none;
  }
</style>
</head>
<body>

  <section class="card card--front">
    <div class="front-brand">
      <h1 class="front-brand__name">LUMEN FRAME</h1>
      <p class="tagline">Architecture Corporate Commercial</p>
    </div>
  </section>

  <section class="card card--back">
    <div class="back-brand">
      <div class="brand-dot"></div>
      <div>
        <h2 class="back-brand__name">LUMEN FRAME</h2>
        <p class="tagline">Architecture Corporate Commercial</p>
      </div>
    </div>

    <div class="person">
      <p class="person__name">DANIEL CARROW</p>
      <p class="person__role">Director</p>
    </div>

    <div class="divider"></div>

    <ul class="contact">
      <li class="contact__item">
        <svg class="contact__icon" viewBox="0 0 16 16"><path fill="#d6ab5a" d="M3.5 1.5l2.5 0 1 3.5-1.8 1.2c.8 1.8 2.2 3.2 4 4l1.2-1.8 3.5 1v2.6c0 .8-.6 1.4-1.4 1.4C6.8 13.4 2.1 8.7 2.1 2.9c0-.8.6-1.4 1.4-1.4z"/></svg>
        555 010 2046
      </li>
      <li class="contact__item">
        <svg class="contact__icon" viewBox="0 0 16 16"><rect x="1.5" y="4" width="13" height="9" rx="1" fill="#d6ab5a"/><path d="M1.8 4.5L8 9l6.2-4.5" fill="none" stroke="#1e1e1e" stroke-width="1.2"/></svg>
        info@lumenframe.com
      </li>
      <li class="contact__item">
        <svg class="contact__icon" viewBox="0 0 16 16"><circle cx="8" cy="8" r="6.5" fill="none" stroke="#d6ab5a" stroke-width="1.6"/><path d="M1.5 8h13M8 1.5c-2.4 2.6-2.4 10.4 0 13M8 1.5c2.4 2.6 2.4 10.4 0 13" fill="none" stroke="#d6ab5a" stroke-width="1.2"/></svg>
        www.lumenframe.com
      </li>
    </ul>
  </section>

</body>
</html>
```